BRIGHT RIVER POWER.

I'd like my business logo.
contact name: Dennis Halvorsen
phone:0438759164
email: info@brightriverpower.net.au
website: www.brightriverpower.net.au

services:
solar
battery storage
LED lighting
energy saving solutions
general electrical
I'd like the design to look professional

Target Market(s)

Everyone

Industry/Entity Type

Business

Contact Information for Business Card

as described above

Requirements
Must have
• Id like the colours and the design to work well with my logo.

```html
<!DOCTYPE html>
<html lang="en">
<head>
<meta charset="utf-8">
<title>Bright River Power – Business Card</title>
<link rel="stylesheet" href="https://fonts.googleapis.com/css2?family=Lato:wght@400;700;900&display=swap">
<style>
  :root {
    --stage: #2b2b2b;
    --paper: #f7f7f5;
    --leaf: #8cba2c;
    --leaf-deep: #6f9a1c;
    --sun: #f0a01a;
    --sun-deep: #c97f0c;
    --brand: #3f9b3a;
    --ink: #1f2414;
    --name: #e4ecd2;
  }
  * { margin: 0; padding: 0; box-sizing: border-box; }
  html, body {
    width: 1200px; height: 873px; overflow: hidden;
    background: var(--stage);
    font-family: "Lato", sans-serif;
  }
  .card {
    position: absolute; left: 150px; top: 180px;
    width: 900px; height: 514px;
    background: var(--paper);
    overflow: hidden;
  }
  .card__wave { position: absolute; inset: 0; }
  .brand {
    position: absolute; left: 250px; top: 110px;
    display: flex; align-items: center; gap: 16px;
  }
  .brand__dot {
    width: 40px; height: 40px; border-radius: 50%;
    background: var(--sun);
  }
  .brand__name {
    font-weight: 900; font-size: 40px; letter-spacing: 1px;
    color: var(--brand);
  }
  .owner {
    position: absolute; left: 620px; top: 222px; text-align: right; width: 220px;
  }
  .owner__name {
    font-weight: 900; font-size: 24px; color: var(--name);
  }
  .owner__role {
    font-size: 17px; color: var(--ink); margin-top: 2px;
  }
  .contact {
    position: absolute; left: 70px; top: 330px;
    color: #fff; font-size: 21px;
  }
  .contact__row { display: flex; align-items: center; gap: 10px; margin-bottom: 8px; }
  .contact__icon { width: 24px; height: 24px; flex: none; }
  .contact__web { font-weight: 900; font-size: 22px; margin-top: 4px; letter-spacing: .3px; }
  .services {
    position: absolute; left: 70px; bottom: 34px;
    font-weight: 900; font-size: 18px; color: var(--ink);
    word-spacing: 2px;
  }
  .services__sep { color: #fff; font-weight: 400; margin: 0 8px; }
</style>
</head>
<body>
  <main class="card">
    <svg class="card__wave" viewBox="0 0 900 514" aria-hidden="true">
      <path d="M0 282 C 220 250, 460 290, 650 200 C 760 150, 840 100, 900 80 L900 514 L0 514 Z" fill="var(--sun-deep)"/>
      <path d="M0 284 C 220 250, 460 292, 650 202 C 760 152, 840 104, 900 86 L900 514 L0 514 Z" fill="var(--sun)"/>
      <path d="M0 308 C 240 270, 480 305, 680 215 C 780 170, 850 125, 900 110 L900 514 L0 514 Z" fill="var(--leaf)"/>
    </svg>

    <div class="brand">
      <span class="brand__dot"></span>
      <span class="brand__name">BRIGHT RIVER POWER</span>
    </div>

    <div class="owner">
      <p class="owner__name">Dennis Halvorsen</p>
      <p class="owner__role">Owner / Founder</p>
    </div>

    <div class="contact">
      <p class="contact__row">
        <svg class="contact__icon" viewBox="0 0 24 24" aria-hidden="true">
          <circle cx="12" cy="12" r="12" fill="var(--sun)"/>
          <path d="M7 9 a5 3 0 0 1 10 0 l-2 1 -1 -2 h-4 l-1 2 z M8 12 h8 v5 h-8 z" fill="#fff"/>
        </svg>
        0438759164
      </p>
      <p class="contact__row">
        <svg class="contact__icon" viewBox="0 0 24 24" aria-hidden="true">
          <circle cx="12" cy="12" r="12" fill="var(--sun)"/>
          <rect x="6" y="8" width="12" height="8" fill="#fff"/>
          <path d="M6 8 L12 13 L18 8" fill="none" stroke="var(--sun)" stroke-width="1.4"/>
        </svg>
        info@brightriverpower.net.au
      </p>
      <p class="contact__web">www.brightriverpower.net.au</p>
    </div>

    <p class="services">
      Solar<span class="services__sep">/</span>LED Lighting<span class="services__sep">/</span>Battery Storage<span class="services__sep">/</span>General Electrical<span class="services__sep">/</span>Energy Saving Solutions
    </p>
  </main>
</body>
</html>
```